Health Supplement Series for 60 tablets of pure Amber Vine Core powder

We need a packaging design theme for a health supplement for international consumers. Our initial product is called 'Amber Vine Core'. It is for general health and is particularly effective for diabetic symptoms.
We would like to see designs that are clean and fresh.
It should give the impression of professional, premium pharmaceutical grade products.
Our company logo is attached below.

Target Market(s)

International

Industry/Entity Type

Health And Wellness

Font styles to use
Serif
Sans Serif

Requirements
Must have
• Bottle and box packaging required.
• 1st product is bottle of 60 tablets of 0.5gm each.
Should not have
• Seals and other "must buy" "guaranteed" etc

```html
<!DOCTYPE html>
<html lang="en">
<head>
<meta charset="utf-8">
<title>Amber Vine Core – Label</title>
<link href="https://fonts.googleapis.com/css2?family=Lato:wght@700;900&family=Arimo:wght@400&display=swap" rel="stylesheet">
<style>
  :root {
    --backdrop: #ececec;
    --label-white: #ffffff;
    --orange-deep: #e2541a;
    --orange-light: #ef7d4f;
    --brand-green: #4f8a1e;
    --body-grey: #3a3a3a;
    --seed-brown: #8a4a22;
    --seed-dark: #3b2216;
  }
  html, body {
    margin: 0;
    width: 1158px;
    height: 1200px;
    overflow: hidden;
    background: var(--backdrop);
  }
  .label {
    position: absolute;
    left: 259px;
    top: 200px;
    width: 640px;
    height: 800px;
    background: var(--label-white);
  }
  .label-art {
    display: block;
    width: 640px;
    height: 800px;
  }
  .brand-name {
    font-family: "Lato", sans-serif;
    font-weight: 700;
    fill: var(--brand-green);
  }
  .product-name {
    font-family: "Lato", sans-serif;
    font-weight: 900;
    fill: var(--label-white);
    font-size: 53px;
    text-anchor: middle;
  }
  .side-copy {
    font-family: "Arimo", sans-serif;
    font-size: 9.4px;
    fill: var(--body-grey);
  }
</style>
</head>
<body>
  <div class="label">
    <svg class="label-art" viewBox="0 0 424 530" xmlns="http://www.w3.org/2000/svg">
      <defs>
        <linearGradient id="panelGradient" x1="0" y1="0" x2="1" y2="0">
          <stop offset="0" stop-color="var(--orange-deep)"/>
          <stop offset="1" stop-color="var(--orange-light)"/>
        </linearGradient>
        <radialGradient id="seedGradient" cx="0.5" cy="0.5" r="0.5">
          <stop offset="0" stop-color="var(--seed-brown)"/>
          <stop offset="1" stop-color="var(--seed-dark)"/>
        </radialGradient>
      </defs>

      <path class="name-panel" fill="url(#panelGradient)"
        d="M329,45 C305,120 255,145 150,165 C88,178 58,205 58,262 L58,410
           C58,460 82,482 130,482 C212,482 272,470 302,450
           C323,435 328,410 328,380 Z"/>

      <g class="brand-lockup">
        <rect x="135" y="96" width="11" height="26" fill="var(--brand-green)"/>
        <text class="brand-name" x="150" y="112" font-size="15" letter-spacing="0.6">NERIDA</text>
        <text class="brand-name" x="150" y="122" font-size="6.2" letter-spacing="0.2">LIFE SCIENCES</text>
      </g>

      <g class="product-title">
        <text class="product-name" x="199" y="251">AMBER</text>
        <text class="product-name" x="199" y="313">VINE</text>
        <text class="product-name" x="199" y="375">CORE</text>
      </g>

      <ellipse class="seed-photo" role="img" aria-label="Photo of dried amber vine seeds and pods"
        cx="202" cy="413" rx="55" ry="24" fill="url(#seedGradient)"/>

      <g class="side-copy" transform="translate(363 440) rotate(-90)">
        <text x="0" y="0">Dietary supplement. 60 tablets of 0.5 g each. Take one</text>
        <text x="0" y="11">tablet twice daily with water after meals.</text>
      </g>
    </svg>
  </div>
</body>
</html>
```